Gooey Tides

I am creating an online slime shop that will sell handmade custom slimes. I need to be able to have payment/shipping options and the ability to change product photos since the product and product name will change often

Target Market(s)

Slime

Industry/Entity Type

Retail - online sales

Coding

Coded - Design and coding required

Number of Pages Required

2 page

Font styles to use
Sans Serif

Colors
0094D4
00A9DD
6FCCEA
C7EBF8
E9F6FB
E54698
E96AAD
F1A4CE
F9D9EA
FCEFF6
A7469A
B969AE
D3A5CF
EDDBEB
F8F0F9

Requirements
Must have
• My logo, my domain, ability to change photos of products for sale, payment options, shipping options, social media links, contact us,

```html
<!DOCTYPE html>
<html lang="en">
<head>
<meta charset="utf-8">
<title>Gooey Tides – Handmade Custom Slimes</title>
<link href="https://fonts.googleapis.com/css2?family=Roboto:wght@400;500;700&display=swap" rel="stylesheet">
<style>
:root{
  --ink:#111111;
  --white:#ffffff;
  --sky:#E9F6FB;
  --sky-mid:#C7EBF8;
  --aqua:#6FCCEA;
  --plum:#A7469A;
  --plum-soft:#B969AE;
  --pink:#E54698;
  --pink-soft:#E96AAD;
  --violet:#7b3cc8;
  --footer:#1c1c1e;
  --line:#dcdcdc;
  --btn:linear-gradient(90deg,#c43fb6 0%,#7b3cc8 100%);
}
*{box-sizing:border-box;margin:0;padding:0}
html,body{width:1200px;height:3780px;overflow:hidden}
body{font-family:'Roboto',Arial,sans-serif;color:var(--ink);background:var(--sky);position:relative}
.abs{position:absolute}
a{color:inherit;text-decoration:none}

/* header */
.site-header{left:0;top:0;width:1200px;height:83px;background:var(--white)}
.search{left:110px;top:31px;display:flex;align-items:center;gap:16px;font-size:13px;font-weight:500;letter-spacing:1px}
.brand{left:0;width:1200px;top:28px;text-align:center;font-size:22px;font-weight:700;color:var(--plum);letter-spacing:1px}
.brand span{display:inline-block;width:12px;height:12px;border-radius:50%;background:var(--plum);margin-right:8px;vertical-align:middle}
.header-icons{right:110px;top:30px;display:flex;gap:20px}

/* hero */
.hero{left:0;top:83px;width:1200px;height:600px}
.hero-media{position:absolute;inset:0;background:radial-gradient(ellipse at 50% 80%,#8fd6b6 0%,#5a8f4a 35%,#2f4a2c 70%,#1e2420 100%)}
.main-nav{left:0;width:1200px;top:50px;display:flex;justify-content:center;gap:28px;font-size:16px;font-weight:700;color:var(--white)}
.main-nav .active{color:var(--pink-soft);text-decoration:underline}
.hero-kicker{left:0;width:1200px;top:224px;text-align:center;color:var(--white);font-size:16px;font-weight:500}
.hero-title{left:0;width:1200px;top:262px;text-align:center;color:var(--white);font-size:58px;font-weight:500;letter-spacing:1px}
.btn{display:flex;align-items:center;justify-content:center;background:var(--btn);color:var(--white);border-radius:27px;font-size:16px;font-weight:500}
.hero .btn{left:519px;top:367px;width:162px;height:53px}
.slider-ctrl{left:1126px;top:247px;width:34px;height:90px}

/* promos */
.promo{overflow:hidden}
.promo-summer{left:112px;top:773px;width:449px;height:406px;background:linear-gradient(135deg,#e8e6e4,#cfc9c5)}
.promo-summer .media{position:absolute;left:215px;top:30px;width:190px;height:350px;background:linear-gradient(180deg,#2d7a95,#0f4b63);border-radius:40% 40% 30% 30%}
.promo-text{position:absolute;left:31px;z-index:1}
.kicker{font-size:18px;font-weight:500}
.promo-heading{font-size:28px;font-weight:700;line-height:39px}
.shop-link{display:flex;align-items:center;gap:14px;font-size:18px;font-weight:700}
.promo-collections{left:587px;top:773px;width:501px;height:187px;background:#9adedb;color:var(--white)}
.promo-deals{left:587px;top:990px;width:501px;height:187px;background:linear-gradient(90deg,#7c7cb2,#c9c3e4);color:var(--white)}
.promo-side .promo-text{left:25px}
.promo-side .promo-heading{font-size:23px;font-weight:500;line-height:30px}
.promo-side .shop-link{font-weight:500;font-size:17px}
.thumb{position:absolute;border-radius:45%}

/* sections */
.section-title{left:0;width:1200px;text-align:center;font-size:38px;font-weight:500;color:var(--plum)}
.card{background:var(--white);border:1px solid var(--line);width:296px;height:317px;text-align:center}
.card .media{position:absolute;left:30px;top:20px;width:236px;height:190px;border-radius:45%}
.card .name{position:absolute;left:0;width:100%;top:242px;font-size:16px}
.card .price{position:absolute;left:0;width:100%;top:271px;font-size:16px;font-weight:500}
.card .add{position:absolute;left:0;width:100%;top:271px;font-size:16px;font-weight:500;color:var(--pink);text-decoration:underline}

/* banner */
.banner{left:0;top:1896px;width:1200px;height:328px;background:linear-gradient(120deg,#a7469a 0%,#a7469a 60%,#9a3f8f 100%)}
.banner-title{left:109px;top:40px;color:var(--white);font-size:32px;font-weight:500;line-height:47px}
.banner-sub{left:118px;top:166px;color:var(--white);font-size:17px}
.banner .btn-white{left:109px;top:210px;width:163px;height:53px;background:var(--white);color:var(--plum);border-radius:27px;display:flex;align-items:center;justify-content:center;font-size:17px;font-weight:700}
.banner .media{left:632px;top:30px;width:446px;height:255px;border-radius:30px;background:linear-gradient(90deg,#2fd3df,#6a4fb0 55%,#27c9d6)}

.tabs{left:0;width:1200px;top:2394px;display:flex;justify-content:center;gap:46px;font-size:16px;font-weight:500}
.tabs .on{position:relative}
.tabs .on::after{content:"";position:absolute;left:8px;right:8px;bottom:-9px;height:2px;background:var(--pink)}

/* footer */
.site-footer{left:0;top:3383px;width:1200px;height:397px;background:var(--footer);color:var(--white)}
.f-col h4{font-size:17px;font-weight:500;letter-spacing:.3px}
.f-col h4::after{content:"";display:block;width:48px;height:2px;background:var(--aqua);margin-top:12px}
.f-col ul{list-style:none;margin-top:20px}
.f-col li{font-size:16px;line-height:30px}
.contact li{display:flex;gap:12px;align-items:flex-start}
.contact svg{flex:none;margin-top:8px}
.pay-grid{display:grid;grid-template-columns:repeat(4,44px);gap:6px;margin-top:22px}
.pay-grid span{height:26px;border-radius:3px;background:var(--white)}
.socials{display:flex;gap:14px;margin-top:22px}
.socials span{width:24px;height:24px;border-radius:50%;background:var(--aqua)}
.f-rule{left:110px;top:329px;width:978px;height:1px;background:#3a3a3c}
.copyright{left:0;width:1200px;top:354px;text-align:center;font-size:16px}
</style>
</head>
<body>

<header class="site-header abs">
  <div class="search abs">
    <svg width="22" height="22" viewBox="0 0 22 22" fill="none" stroke="#222" stroke-width="1.8"><circle cx="9.5" cy="9.5" r="7.5"/><path d="M15 15l5 5"/></svg>
    SEARCH
  </div>
  <div class="brand abs"><span></span>Gooey Tides</div>
  <div class="header-icons abs">
    <svg width="24" height="24" viewBox="0 0 24 24" fill="none" stroke="#222" stroke-width="1.6"><path d="M4 8h16l-1 14H5z"/><path d="M8 8V6a4 4 0 0 1 8 0v2"/></svg>
    <svg width="26" height="24" viewBox="0 0 26 24" fill="none" stroke="#222" stroke-width="1.6"><path d="M13 22S2 15 2 8a5.5 5.5 0 0 1 11-1 5.5 5.5 0 0 1 11 1c0 7-11 14-11 14z"/></svg>
    <svg width="24" height="24" viewBox="0 0 24 24" fill="none" stroke="#222" stroke-width="1.6"><circle cx="12" cy="12" r="10.5"/><circle cx="12" cy="10" r="3.5"/><path d="M5.5 19c2-3 4-4 6.5-4s4.5 1 6.5 4"/></svg>
  </div>
</header>

<section class="hero abs">
  <div class="hero-media" role="img" aria-label="Green moss slime scene with a small tree and panda figures on mint slime"></div>
  <nav class="main-nav abs">
    <a class="active">Home</a><a>Category</a><a>Products</a><a>Shop</a><a>Blog</a><a>Contact</a>
  </nav>
  <p class="hero-kicker abs">HANDMADE CUSTOM SLIMES</p>
  <h1 class="hero-title abs">GOOEY TIDES</h1>
  <a class="btn abs">GET STARTED</a>
  <svg class="slider-ctrl abs" viewBox="0 0 34 90" fill="none" stroke="#fff" stroke-width="2"><path d="M3 16L17 3l14 13"/><circle cx="17" cy="45" r="2.5" fill="#fff" stroke="none"/><path d="M3 74l14 13 14-13"/></svg>
</section>

<article class="promo promo-summer abs">
  <div class="media" role="img" aria-label="Hand stretching dark teal slime"></div>
  <div class="promo-text" style="top:52px">
    <p class="kicker">SUMMER SALE</p>
    <h2 class="promo-heading" style="margin-top:12px">NOW SAVE<br>UPTO20%</h2>
  </div>
  <a class="promo-text shop-link" style="top:342px">SHOP NOW
    <svg width="20" height="10" viewBox="0 0 20 10"><path d="M0 5h17M13 1l5 4-5 4" stroke="#111" stroke-width="2" fill="none"/></svg></a>
</article>

<article class="promo promo-side promo-collections abs">
  <div class="thumb" role="img" aria-label="Blue slime with green moss islands" style="left:298px;top:25px;width:165px;height:135px;background:linear-gradient(135deg,#3cc1e6,#1b8fc4)"></div>
  <div class="promo-text" style="top:22px">
    <p class="kicker" style="font-size:17px">SALE OFF</p>
    <h2 class="promo-heading" style="margin-top:8px">GREAT COLLECTIONS</h2>
  </div>
  <a class="promo-text shop-link" style="top:144px">SHOP NOW
    <svg width="20" height="10" viewBox="0 0 20 10"><path d="M0 5h17M13 1l5 4-5 4" stroke="#fff" stroke-width="2" fill="none"/></svg></a>
</article>

<article class="promo promo-side promo-deals abs">
  <div class="thumb" role="img" aria-label="Purple dripping slime cake" style="left:275px;top:12px;width:192px;height:168px;border-radius:20px;background:linear-gradient(180deg,#c24ad6,#5a2fb8)"></div>
  <div class="promo-text" style="top:20px">
    <p class="kicker" style="font-size:17px">NEW</p>
    <h2 class="promo-heading" style="margin-top:6px">SHOP TODAY's DEALS<br>&amp; OFFERS</h2>
  </div>
  <a class="promo-text shop-link" style="top:145px">SHOP NOW
    <svg width="20" height="10" viewBox="0 0 20 10"><path d="M0 5h17M13 1l5 4-5 4" stroke="#fff" stroke-width="2" fill="none"/></svg></a>
</article>

<h2 class="section-title abs" style="top:1280px">NEW ARRIVALS</h2>

<div class="card abs" style="left:112px;top:1373px">
  <div class="media" role="img" aria-label="Teal bubbly slime with a yellow duck charm" style="background:linear-gradient(135deg,#1f8fb0,#0d5e7d)"></div>
  <p class="name">CUSTOM SLIMES 01</p><p class="price">$49.99</p>
</div>
<div class="card abs" style="left:453px;top:1373px">
  <div class="media" role="img" aria-label="Jar of pale blue slime topped with charms" style="border-radius:20px;background:linear-gradient(180deg,#c9d3d6,#8fb4bd)"></div>
  <p class="name">CUSTOM SLIMES 02</p><a class="add">ADD TO CART</a>
</div>
<div class="card abs" style="left:793px;top:1373px">
  <div class="media" role="img" aria-label="Bright blue slime with moss islands" style="background:linear-gradient(135deg,#3cc1e6,#1b8fc4)"></div>
  <p class="name">CUSTOM SLIMES 03</p><p class="price">$49.99</p>
</div>

<a class="btn abs" style="left:520px;top:1758px;width:163px;height:53px">VIEW ALL</a>

<section class="banner abs">
  <h2 class="banner-title abs">YOUR BEST SOURCE OF<br>HANDMADE SLIMES</h2>
  <p class="banner-sub abs">Products made with love.</p>
  <a class="btn-white abs">SHOP</a>
  <div class="media abs" role="img" aria-label="Turquoise and purple jelly slime cubes"></div>
</section>

<h2 class="section-title abs" style="top:2305px">HANDMADE FOR YOU</h2>
<div class="tabs abs"><a class="on">FEATURED</a><a>TRENDING</a><a>BEST SELLER</a></div>

<div class="card abs" style="left:110px;top:2496px">
  <div class="media" role="img" aria-label="Hand holding glittery blue slime" style="background:linear-gradient(135deg,#9fb8e6,#4d6fd0)"></div>
  <p class="name">CUSTOM SLIMES 01</p><p class="price">$49.99</p>
</div>
<div class="card abs" style="left:452px;top:2496px">
  <div class="media" role="img" aria-label="Grey marbled putty splash" style="background:radial-gradient(circle,#8a86a0,#e6e6ea 70%)"></div>
  <p class="name">CUSTOM SLIMES 02</p><a class="add">ADD TO CART</a>
</div>
<div class="card abs" style="left:792px;top:2496px">
  <div class="media" role="img" aria-label="Round blue cloud slime" style="background:radial-gradient(circle,#6fd6f0,#2fa6d8 60%,#fff 72%)"></div>
  <p class="name">CUSTOM SLIMES 03</p><p class="price">$49.99</p>
</div>
<div class="card abs" style="left:110px;top:2862px">
  <div class="media" role="img" aria-label="Mint green slime puddle" style="background:radial-gradient(circle,#3aa8a6,#8fd8c8 55%,#fff 72%)"></div>
  <p class="name">CUSTOM SLIMES 04</p><p class="price">$49.99</p>
</div>
<div class="card abs" style="left:452px;top:2862px">
  <div class="media" role="img" aria-label="Blue sea creature shaped squishy" style="background:radial-gradient(circle,#2f6fc4,#6d4bc0 55%,#fff 72%)"></div>
  <p class="name">CUSTOM SLIMES 05</p><a class="add">ADD TO CART</a>
</div>
<div class="card abs" style="left:792px;top:2862px">
  <div class="media" role="img" aria-label="Lilac shimmer slime splash" style="background:radial-gradient(circle,#b57ad8,#d8b8ec 55%,#fff 72%)"></div>
  <p class="name">CUSTOM SLIMES 06</p><p class="price">$49.99</p>
</div>

<a class="btn abs" style="left:519px;top:3237px;width:163px;height:54px">VIEW ALL</a>

<footer class="site-footer abs">
  <div class="f-col abs" style="left:160px;top:52px">
    <h4>QUICK LINKS</h4>
    <ul><li>Home</li><li>Category</li><li>Products</li><li>Shop</li><li>Blog</li><li>Contact</li></ul>
  </div>
  <div class="f-col abs" style="left:340px;top:52px">
    <h4>EXTRAS</h4>
    <ul><li>Our Brands</li><li>Special Offers</li><li>Gift Vouchers</li><li>Affiliates</li></ul>
  </div>
  <div class="f-col contact abs" style="left:527px;top:52px;width:300px">
    <h4>CONTACT US</h4>
    <ul>
      <li><svg width="14" height="14" viewBox="0 0 14 14" fill="none" stroke="#fff" stroke-width="1.5"><circle cx="7" cy="7" r="6"/><path d="M7 3.5V7h3"/></svg>Monday - Friday: 09:00 - 18:30</li>
      <li><svg width="14" height="14" viewBox="0 0 14 14"><path d="M7 13S2.5 8 2.5 5a4.5 4.5 0 0 1 9 0C11.5 8 7 13 7 13z" fill="#fff"/><circle cx="7" cy="5" r="1.6" fill="#1c1c1e"/></svg>48 Tidepool Lane, Harbor Row<br>Bay City.</li>
      <li><svg width="14" height="14" viewBox="0 0 14 14"><path d="M3 1l2.5 3-1.5 1.5a8 8 0 0 0 4.5 4.5L10 8.5l3 2.5-1.5 2C6 13 1 8 1 2.5z" fill="#fff"/></svg>+100-555-014-7</li>
      <li><svg width="14" height="14" viewBox="0 0 14 14" fill="none" stroke="#fff" stroke-width="1.4"><rect x="1" y="2.5" width="12" height="9"/><path d="M1 3l6 5 6-5"/></svg>hello@gooeytides.shop</li>
    </ul>
  </div>
  <div class="f-col abs" style="left:845px;top:52px">
    <h4>PAYMENT OPTIONS</h4>
    <div class="pay-grid">
      <span></span><span></span><span></span><span></span>
      <span></span><span></span><span></span><span></span>
      <span></span><span></span><span></span>
    </div>
    <div class="socials"><span></span><span></span><span></span><span></span></div>
  </div>
  <div class="f-rule abs"></div>
  <p class="copyright abs">© 2024 Gooey Tides. All Rights Reserved.</p>
</footer>

</body>
</html>
```